Photographer website, needs Facebook design. (updated details in brief.)

Company name Tobin Velasco Photography, looking to add a Facebook design, that is minimalistic, yet powerful. Less is more in my opinion, but what's there is creative, but eye catchy. see example image in files section for a better idea of what I am looking for. I have also added some source files for my logo.

Target Market(s)

local musicians/artists, models/fashion, and business professional looking for headshots or corporate business profile images.

Colors
0655a3
cfdfed
ffffff

Requirements
Must have
• I have added a screen shot of what I am looking for, for everyone to gain a better sense of my vision. Please see the uploaded files below.
Nice to have
• I am really a fan of the example image in the files section below. Something close to that I would be very happy with.
Should not have
• should not have my face on the cover.

```html
<!DOCTYPE html>
<html lang="en">
<head>
<meta charset="UTF-8">
<title>Tobin Velasco Photography – Cover</title>
<link rel="stylesheet" href="https://fonts.googleapis.com/css2?family=Montserrat:wght@500;600&display=swap">
<style>
  :root {
    --brand-blue: #0655a3;
    --brand-ice: #cfdfed;
    --white: #ffffff;
    --ink: #111418;
    --night: #04101c;
    --night-mid: #0b2a45;
    --neon: #6fd2f2;
    --studio-black: #020405;
    --studio-teal: #1f7d8a;
    --studio-deep: #0a3a42;
    --portrait-navy: #081a2b;
    --portrait-gold: #e0b26a;
    --portrait-denim: #2f7396;
    --fashion-white: #f1f4f6;
    --fashion-yellow: #efe7a4;
    --fashion-mint: #b9e0dc;
    --wedding-amber: #7a4a18;
    --wedding-glow: #f4c77c;
    --wedding-cream: #f6e2c8;
  }
  * { margin: 0; padding: 0; box-sizing: border-box; }
  html, body { width: 1200px; height: 457px; overflow: hidden; background: var(--night); }
  .cover {
    position: relative;
    width: 1200px;
    height: 457px;
    overflow: hidden;
    font-family: "Montserrat", sans-serif;
  }
  .cover__art { position: absolute; inset: 0; width: 1200px; height: 457px; display: block; }
  .brand {
    position: absolute;
    left: 168px;
    top: 30px;
    width: 164px;
    text-align: center;
    color: var(--white);
    font-weight: 500;
    line-height: 1;
  }
  .brand__mark {
    width: 44px; height: 44px;
    margin: 0 auto 18px;
    border: 0;
    background: var(--white);
  }
  .brand__name { display: block; font-size: 23px; letter-spacing: 4px; margin-bottom: 6px; }
  .brand__name + .brand__name { margin-bottom: 12px; }
  .brand__sub { display: block; font-size: 9px; letter-spacing: 3.4px; }
  .section-title {
    position: absolute;
    top: 22px;
    font-size: 19px;
    font-weight: 600;
    letter-spacing: 4.6px;
    line-height: 1;
    color: var(--white);
    white-space: nowrap;
  }
  .section-title--portfolio { right: 553px; }
  .section-title--fashion { right: 309px; color: var(--ink); }
  .section-title--weddings { right: 17px; }
</style>
</head>
<body>
<main class="cover">
  <svg class="cover__art" viewBox="0 0 1200 457" xmlns="http://www.w3.org/2000/svg">
    <defs>
      <linearGradient id="bg-grad" x1="0" y1="0" x2="1" y2="1">
        <stop offset="0" stop-color="var(--night-mid)"/>
        <stop offset="0.55" stop-color="var(--night)"/>
        <stop offset="1" stop-color="var(--brand-blue)"/>
      </linearGradient>
      <radialGradient id="studio-grad" cx="0.5" cy="0.72" r="0.5">
        <stop offset="0" stop-color="var(--studio-teal)"/>
        <stop offset="0.45" stop-color="var(--studio-deep)"/>
        <stop offset="1" stop-color="var(--studio-black)"/>
      </radialGradient>
      <linearGradient id="portrait-base" x1="0" y1="0" x2="1" y2="1">
        <stop offset="0" stop-color="var(--portrait-navy)"/>
        <stop offset="0.55" stop-color="var(--portrait-navy)"/>
        <stop offset="1" stop-color="var(--portrait-denim)"/>
      </linearGradient>
      <radialGradient id="portrait-glow" cx="0.42" cy="0.5" r="0.5">
        <stop offset="0" stop-color="var(--portrait-gold)" stop-opacity="0.95"/>
        <stop offset="0.55" stop-color="var(--portrait-gold)" stop-opacity="0.45"/>
        <stop offset="1" stop-color="var(--portrait-gold)" stop-opacity="0"/>
      </radialGradient>
      <linearGradient id="fashion-grad" x1="0" y1="0" x2="0" y2="1">
        <stop offset="0" stop-color="var(--fashion-white)"/>
        <stop offset="0.38" stop-color="var(--fashion-white)"/>
        <stop offset="0.55" stop-color="var(--fashion-yellow)"/>
        <stop offset="0.72" stop-color="var(--fashion-mint)"/>
        <stop offset="1" stop-color="var(--fashion-white)"/>
      </linearGradient>
      <linearGradient id="wedding-base" x1="0" y1="0" x2="0" y2="1">
        <stop offset="0" stop-color="var(--wedding-amber)"/>
        <stop offset="1" stop-color="#4a2c10"/>
      </linearGradient>
      <radialGradient id="wedding-glow" cx="0.5" cy="0.7" r="0.6">
        <stop offset="0" stop-color="var(--wedding-cream)"/>
        <stop offset="0.5" stop-color="var(--wedding-glow)" stop-opacity="0.75"/>
        <stop offset="1" stop-color="var(--wedding-glow)" stop-opacity="0"/>
      </radialGradient>
      <radialGradient id="wedding-top" cx="0.5" cy="0" r="0.55">
        <stop offset="0" stop-color="var(--wedding-glow)"/>
        <stop offset="1" stop-color="var(--wedding-glow)" stop-opacity="0"/>
      </radialGradient>
    </defs>

    <rect class="backdrop" width="1200" height="457" fill="url(#bg-grad)" role="img" aria-label="Dark blue studio backdrop with glowing neon light bars"/>

    <g class="panel panel--studio" role="img" aria-label="Low-key studio photo of a figure hugging their shoulders in teal rim light">
      <polygon points="105,0 376,0 280,457 2,457" fill="url(#studio-grad)"/>
    </g>
    <g class="panel panel--portfolio" role="img" aria-label="Moody profile portrait of a woman with long blonde hair in a denim shirt">
      <polygon points="385,0 654,0 561,457 288,457" fill="url(#portrait-base)"/>
      <polygon points="385,0 654,0 561,457 288,457" fill="url(#portrait-glow)"/>
    </g>
    <g class="panel panel--fashion" role="img" aria-label="Fashion photo of a dancer in a pastel yellow and mint chiffon skirt on white">
      <polygon points="663,0 932,0 839,457 568,457" fill="url(#fashion-grad)"/>
    </g>
    <g class="panel panel--weddings" role="img" aria-label="Bride in an ivory gown holding a bouquet under warm bokeh lights">
      <polygon points="942,0 1198,0 1117,457 846,457" fill="url(#wedding-base)"/>
      <polygon points="942,0 1198,0 1117,457 846,457" fill="url(#wedding-top)"/>
      <polygon points="942,0 1198,0 1117,457 846,457" fill="url(#wedding-glow)"/>
    </g>

    <g class="panel-edges" stroke="var(--neon)" stroke-width="2" stroke-opacity="0.55">
      <line x1="378" y1="0" x2="282" y2="457"/>
      <line x1="657" y1="0" x2="564" y2="457"/>
      <line x1="936" y1="0" x2="843" y2="457"/>
      <line x1="1200" y1="0" x2="1120" y2="457"/>
    </g>
  </svg>

  <div class="brand">
    <div class="brand__mark"></div>
    <span class="brand__name">TOBIN</span>
    <span class="brand__name">VELASCO</span>
    <span class="brand__sub">PHOTOGRAPHY</span>
  </div>

  <h2 class="section-title section-title--portfolio">PORTFOLIO</h2>
  <h2 class="section-title section-title--fashion">FASHION</h2>
  <h2 class="section-title section-title--weddings">WEDDINGS</h2>
</main>
</body>
</html>
```